Financial Services Consultant needs a business card

We need a business card for a new consulting company based in Melbourne called
"Quelbrook Insights". Tagline is Measure, Monitor, Save
We would like to see business card designs that are in line with the minimal style of the website www.quelbrook-insights.example
The font I have used on the website is Proxima Nova and would like the same or similar font used on the business card with a minimal design in line with the website Two sided with "QUELBROOK INSIGHTS" MEASURE, MONITOR, SAVE on one side and name, title and contact details on the otther
Updates

Hi All, thanks for your submissions, much appreciated.

I have recently added some colour to my webiste, it is hex #3a7b74 for those that wish to use it
Thanks

Hi all

thanks very much for your design submissions I am very impressed and they are much appreciated.

Interms of general feedback please find below;

Colour: I am trying to stick to a minimal design and colour scheme for my website which is still under construction, up to 3 colours( www.quelbrook-insights.example) it is currently black and white with a small amount of blue/green but I am open to suggestion/interpretations for a consulting company.

Card: I dont mind if it has rounded edges or straight, I was thinking about using a letterpress card if possible

Detail: the detail on the card will include; Name, Title, Mobile, Personal Email, Business Email,Web,Business Address

Once again thanks for submissions

Industry/Entity Type

Business

```html
<!DOCTYPE html>
<html lang="en">
<head>
<meta charset="utf-8">
<title>Quelbrook Insights — Business Card</title>
<link rel="stylesheet" href="https://fonts.googleapis.com/css2?family=Exo+2:wght@600;700&family=Saira+Condensed:wght@500;600;700&display=swap">
<style>
  :root {
    --paper: #e9eaea;
    --teal: #3a7b74;
    --teal-light: #5aa79d;
    --teal-dark: #2c4b47;
    --teal-top: #26403c;
    --ink: #23302f;
    --white: #f4f6f5;
    --soft-white: #e3e6e5;
    --card-shadow: 0 18px 40px rgba(0,0,0,.22);
  }
  * { box-sizing: border-box; margin: 0; padding: 0; }
  html, body { width: 1200px; height: 900px; overflow: hidden; }
  body {
    background: var(--paper);
    position: relative;
    font-family: "Saira Condensed", "Arial Narrow", sans-serif;
  }
  .card {
    position: absolute;
    left: 290px;
    width: 620px;
    height: 354px;
    overflow: hidden;
    box-shadow: var(--card-shadow);
  }
  .card--contact { top: 70px; background: var(--ink); }
  .card--brand { top: 476px; background: var(--teal); }

  .card__shapes { position: absolute; inset: 0; width: 100%; height: 100%; }

  .brand-title {
    position: absolute;
    font-family: "Exo 2", "Segoe UI", sans-serif;
    font-weight: 700;
    color: var(--white);
    letter-spacing: .5px;
    white-space: nowrap;
    line-height: 1.1;
  }
  .card--contact .brand-title { left: 40px; top: 48px; font-size: 32px; }

  .name-tab {
    position: absolute;
    right: 24px;
    top: 146px;
    text-align: right;
    color: var(--ink);
    line-height: 1;
  }
  .name-tab__name { font-size: 22px; font-weight: 700; letter-spacing: 1px; }
  .name-tab__role { font-size: 15px; font-weight: 700; letter-spacing: 1px; margin-top: 1px; }

  .contact-list {
    position: absolute;
    right: 22px;
    top: 206px;
    list-style: none;
    color: var(--white);
    font-size: 13.5px;
    font-weight: 500;
    letter-spacing: 1px;
  }
  .contact-list li {
    display: flex;
    justify-content: flex-end;
    align-items: center;
    gap: 14px;
    height: 25px;
    white-space: nowrap;
  }
  .contact-list svg { width: 15px; height: 15px; flex: none; fill: none; stroke: var(--white); stroke-width: 1.6; opacity: .85; }

  .band { position: absolute; left: 0; right: 0; height: 34px; background: var(--teal-dark); }
  .band--top { top: 0; }
  .band--bottom { bottom: 0; }

  .brand-block {
    position: absolute;
    left: 0; right: 0; top: 112px;
    text-align: center;
    color: var(--soft-white);
  }
  .card--brand .brand-title { position: static; font-size: 44px; color: var(--soft-white); }
  .brand-web {
    margin-top: 4px;
    font-size: 24px;
    font-weight: 600;
    letter-spacing: 2px;
    line-height: 1.1;
  }
  .brand-tagline {
    margin-top: 12px;
    font-size: 16px;
    font-weight: 600;
    letter-spacing: 5px;
    line-height: 1;
    color: var(--teal-light);
    filter: brightness(1.25);
  }
</style>
</head>
<body>

  <section class="card card--contact" aria-label="Business card, contact side">
    <svg class="card__shapes" viewBox="0 0 620 354" preserveAspectRatio="none" aria-hidden="true">
      <rect x="0" y="0" width="620" height="18" fill="#26403c"/>
      <polygon points="0,18 620,18 620,150 265,150 212,212 160,150 0,150" fill="#3a7b74"/>
      <polygon points="420,132 620,132 620,194 380,194" fill="#5aa79d"/>
    </svg>

    <h1 class="brand-title">QUELBROOK INSIGHTS</h1>

    <div class="name-tab">
      <p class="name-tab__name">YOUR NAME</p>
      <p class="name-tab__role">YOUR DESIGNATION</p>
    </div>

    <ul class="contact-list">
      <li>+61 400 123 456
        <svg viewBox="0 0 16 16"><rect x="4" y="1.5" width="8" height="13" rx="1.5"/><line x1="7" y1="12" x2="9" y2="12"/></svg>
      </li>
      <li>YOURNAME@MAILBOX.EXAMPLE
        <svg viewBox="0 0 16 16"><rect x="1.5" y="3.5" width="13" height="9" rx="1"/><polyline points="1.5,4 8,9 14.5,4"/></svg>
      </li>
      <li>INFO@QUELBROOK-INSIGHTS.EXAMPLE
        <svg viewBox="0 0 16 16"><rect x="1.5" y="3.5" width="13" height="9" rx="1"/><polyline points="1.5,4 8,9 14.5,4"/></svg>
      </li>
      <li>WWW.QUELBROOK-INSIGHTS.EXAMPLE
        <svg viewBox="0 0 16 16"><circle cx="8" cy="8" r="6.5"/><ellipse cx="8" cy="8" rx="2.8" ry="6.5"/><line x1="1.5" y1="8" x2="14.5" y2="8"/></svg>
      </li>
      <li>12 LORNEVALE ST, MELBOURNE VIC 3000
        <svg viewBox="0 0 16 16"><path d="M8 15 C8 15 3 9.5 3 6 A5 5 0 0 1 13 6 C13 9.5 8 15 8 15 Z"/><circle cx="8" cy="6" r="1.8"/></svg>
      </li>
    </ul>
  </section>

  <section class="card card--brand" aria-label="Business card, brand side">
    <div class="band band--top"></div>
    <div class="band band--bottom"></div>
    <div class="brand-block">
      <h2 class="brand-title">QUELBROOK INSIGHTS</h2>
      <p class="brand-web">WWW.QUELBROOK-INSIGHTS.EXAMPLE</p>
      <p class="brand-tagline">MEASURE, MONITOR, SAVE</p>
    </div>
  </section>

</body>
</html>
```